Wordpress Design Project

Need a page like this but with your own personal twist

I will provide you the iframed form on 2nd page

http://www.brightpolicysaver.example/index1178.php?subid=8715815

Requirements
Must have
• Article with link out
must pass zipcode to iframed form on 2nd page.

Must provide css for form pages.

```html
<!DOCTYPE html>
<html lang="en">
<head>
<meta charset="utf-8">
<title>Auto-Insurance – Save Big on Your Auto Insurance</title>
<link rel="stylesheet" href="https://fonts.googleapis.com/css2?family=Fjalla+One&family=Open+Sans:wght@400;600&family=Oswald:wght@400;500&family=Archivo+Black&display=swap">
<style>
:root{
  --navy:#0c2d5c;
  --red:#d71f26;
  --red-dark:#b5141a;
  --yellow:#ffd21e;
  --ink:#111;
  --panel:#e8e8e8;
  --footer:#0c1220;
  --hero-top:#1f4f95;
  --hero-bottom:#5d93c6;
}
*{box-sizing:border-box;margin:0;padding:0}
html,body{width:1046px;height:1200px;overflow:hidden}
body{position:relative;background:#f4f4f4;font-family:Arial,Helvetica,sans-serif;color:var(--ink)}

.site-header{position:absolute;left:0;top:0;width:1046px;height:115px;
  background:repeating-linear-gradient(0deg,#f3f3f3 0 2px,#fff 2px 4px);border-top:7px solid var(--navy)}
.brand{position:absolute;left:121px;top:36px}
.brand-name{font-family:"Archivo Black",sans-serif;font-size:36px;color:var(--red);line-height:1}
.brand-tagline{font-family:"Open Sans",sans-serif;font-size:13px;letter-spacing:4.1px;color:#222;margin-top:8px}
.call{position:absolute;left:684px;top:44px;font-family:"Oswald",sans-serif;font-size:25px;color:var(--navy);font-weight:500}
.call span{color:var(--red);margin-right:8px}

.hero-band{position:absolute;left:0;top:115px;width:1046px;height:519px;background:var(--navy)}
.hero-frame{position:absolute;left:112px;top:142px;width:820px;height:465px;background:#d9d9d9}
.hero-scene{position:absolute;left:9px;top:9px;width:802px;height:447px;
  background:linear-gradient(180deg,var(--hero-top),var(--hero-bottom))}
.hero-copy{position:absolute;left:155px;top:168px;width:280px;color:#fff;font-family:"Open Sans",sans-serif}
.hero-price{font-family:"Oswald",sans-serif;color:var(--yellow);font-size:28px;font-weight:500;line-height:70px}
.hero-price strong{font-size:50px;font-weight:500}
.hero-lead{font-size:28px;line-height:35px}

.quote-card{position:absolute;left:485px;top:127px;width:403px;height:459px;background:#fff;border-radius:4px;text-align:center}
.quote-card::before,.quote-card::after{content:"";position:absolute;top:0;width:18px;height:18px;background:var(--red);border-radius:6px 6px 0 0}
.quote-card::before{left:-18px}
.quote-card::after{right:-18px}
.quote-title{font-family:"Oswald",sans-serif;font-weight:500;color:var(--red);font-size:38px;line-height:1;margin-top:7px}
.quote-sub{font-family:"Oswald",sans-serif;font-weight:500;color:var(--navy);font-size:30px;line-height:1;margin-top:4px}
.steps{display:flex;justify-content:space-between;margin-top:8px}
.step{width:134px;font-family:"Open Sans",sans-serif;font-size:14.5px;color:#333;line-height:18px}
.step svg{display:block;margin:0 auto 4px}
.step em{font-style:normal;color:var(--red)}
.zip-box{position:relative;margin:40px auto 0;width:350px;height:52px;background:var(--panel)}
.zip-label{position:absolute;left:58px;top:-34px;width:234px;height:34px;background:var(--panel);border-radius:10px 10px 0 0;
  font-family:"Open Sans",sans-serif;font-size:16px;line-height:34px;color:#222}
.zip-input{position:absolute;left:76px;top:12px;width:202px;height:28px;border:1px solid #999;border-radius:6px;background:#fff}
.continue{display:inline-flex;align-items:center;gap:10px;margin-top:2px;height:42px;padding:0 22px;border-radius:4px;
  background:linear-gradient(#e0262d,var(--red-dark));color:#fff;font-family:"Archivo Black",sans-serif;font-size:23px;border:0}
.secure-note{font-family:"Courier New",monospace;font-size:10px;color:#444;margin-top:8px}
.seal{display:block;width:115px;height:40px;margin:10px auto 0;background:#d9d9d9;border-radius:3px}

.content{position:absolute;left:0;top:634px;width:1046px;height:494px;
  background:linear-gradient(180deg,#e9e9e9 0,#fafafa 40px,#fff 80px)}
.article{position:absolute;left:110px;top:22px;width:532px}
.article h1{font-family:"Fjalla One",sans-serif;font-weight:400;font-size:28px;color:#111}
.article p{font-size:13.2px;line-height:15.8px;color:#111;margin-top:14px}
.article p + p{margin-top:16px}
.article .try-link{display:block;margin-top:24px;color:var(--red);font-style:italic;font-size:15px}

.reviews{position:absolute;left:693px;top:26px;width:241px}
.reviews h2{font-family:"Fjalla One",sans-serif;font-weight:400;font-size:22px;color:#111;display:flex;align-items:center;gap:8px}
.review-text{font-style:italic;font-size:14px;line-height:17.5px;color:#222;margin-top:20px;width:241px}
.review-name{text-align:right;font-style:italic;font-size:12px;color:var(--red);margin-top:8px;padding-right:10px;
  padding-bottom:10px;border-bottom:1px dashed #bbb}
.social-box{position:absolute;left:693px;top:237px;width:241px;height:233px;border:1px solid #aab;border-top:2px solid #5a74a8;background:#fff;font-size:9px;color:#333}
.social-head{background:#eef0f4;padding:6px 8px;font-size:11px;font-weight:bold;color:#222}
.social-page{display:flex;gap:8px;padding:6px 5px}
.social-mark{width:42px;height:42px;border:1px solid #ccc;display:flex;align-items:center;justify-content:center}
.social-mark span{width:26px;height:26px;background:var(--red)}
.social-page b{font-weight:400;color:#3b5998;font-size:13px}
.like-btn{display:inline-block;margin-top:3px;width:38px;height:16px;border:1px solid #bbb;background:#f3f3f3}
.fans{display:grid;grid-template-columns:repeat(5,40px);gap:8px 7px;padding:4px 6px;text-align:center}
.fan i{display:block;width:40px;height:40px;margin-bottom:3px;background:linear-gradient(#8a7a66,#4b3f33)}
.social-foot{position:absolute;bottom:4px;left:6px;right:6px;border-top:1px solid #ddd;padding-top:4px;font-size:8px}

.site-footer{position:absolute;left:0;top:1128px;width:1046px;height:72px;background:var(--footer);
  font-size:10px;color:#6a7384;padding:20px 0 0 119px;line-height:13px}
.site-footer a{color:#6a7384;text-decoration:none}
.badge{position:absolute;left:837px;top:29px;width:97px;height:17px;background:#d9d9d9}
</style>
</head>
<body>
<header class="site-header">
  <div class="brand">
    <div class="brand-name">Auto-Insurance</div>
    <div class="brand-tagline">YOUR PUNCH LINE GOSE HERE</div>
  </div>
  <div class="call"><span>Call us:</span>1-800-555-0142</div>
</header>

<section class="hero-band"></section>
<div class="hero-frame">
  <div class="hero-scene" role="img" aria-label="Photo of a silver sedan parked on a beach by the sea under a blue sky"></div>
</div>
<div class="hero-copy">
  <div class="hero-price">AS low as <strong>$7/week</strong></div>
  <p class="hero-lead">Over 300,000 people have used our site to help find &amp; compare discount car insurance rates!</p>
</div>

<form class="quote-card" action="http://www.brightpolicysaver.example/index1178.php?subid=8715815">
  <div class="quote-title">Save Big!</div>
  <div class="quote-sub">on Your Auto Insurance</div>
  <div class="steps">
    <div class="step">
      <svg width="100" height="90" viewBox="0 0 100 90"><path d="M72 15A38 38 0 1 0 82 55" fill="none" stroke="#d71f26" stroke-width="3"/><path d="M64 10L90 30L96 60L80 40Z" fill="#d71f26"/><text x="44" y="40" text-anchor="middle" font-family="Archivo Black,sans-serif" font-size="20" fill="#0c2d5c">Step</text><text x="44" y="64" text-anchor="middle" font-family="Archivo Black,sans-serif" font-size="20" fill="#0c2d5c">1</text></svg>
      Enter your zip<br>code.
    </div>
    <div class="step">
      <svg width="100" height="90" viewBox="0 0 100 90"><path d="M72 15A38 38 0 1 0 82 55" fill="none" stroke="#d71f26" stroke-width="3"/><path d="M64 10L90 30L96 60L80 40Z" fill="#d71f26"/><text x="44" y="40" text-anchor="middle" font-family="Archivo Black,sans-serif" font-size="20" fill="#0c2d5c">Step</text><text x="44" y="64" text-anchor="middle" font-family="Archivo Black,sans-serif" font-size="20" fill="#0c2d5c">2</text></svg>
      Fill out your vehicle<br>&amp; driver information.
    </div>
    <div class="step">
      <svg width="100" height="90" viewBox="0 0 100 90"><path d="M72 15A38 38 0 1 0 82 55" fill="none" stroke="#d71f26" stroke-width="3"/><path d="M64 10L90 30L96 60L80 40Z" fill="#d71f26"/><text x="44" y="40" text-anchor="middle" font-family="Archivo Black,sans-serif" font-size="20" fill="#0c2d5c">Step</text><text x="44" y="64" text-anchor="middle" font-family="Archivo Black,sans-serif" font-size="20" fill="#0c2d5c">3</text></svg>
      Compare rates<br>&amp; <em>save!</em>
    </div>
  </div>
  <div class="zip-box">
    <div class="zip-label">Enter your zip code here!</div>
    <div class="zip-input"></div>
  </div>
  <button class="continue" type="submit">Continue
    <svg width="22" height="22" viewBox="0 0 22 22"><circle cx="11" cy="11" r="10" fill="#fff"/><path d="M8 6L16 11L8 16Z" fill="#c8171d"/></svg>
  </button>
  <div class="secure-note">Your Information is Secure</div>
  <span class="seal"></span>
</form>

<main class="content">
  <article class="article">
    <h1>Save $100's off your auto insurance rates</h1>
    <p>Lorem ipsum dolor sit amet, consectetur adipiscing elit. Cras ut lectus vel lacus dapibus accumsan sed id est. Vestibulum dignissim nulla odio, a pharetra lectus mattis tristique. Pellentesque varius neque in aliquet porta. Nullam commodo tristique mi, ac laoreet magna pellentesque sed. Duis ultricies, eros sed feugiat placerat, leo velit cursus nisi, et dapibus tellus ligula non metus. Nulla risus felis, pretium a dictum id, lobortis sit amet erat. Ut lorem nisl, lobortis ut ligula vel, placerat suscipit risus. In venenatis justo tortor, in luctus ligula tincidunt et. Duis dapibus viverra diam, id tincidunt dolor pharetra nec. Proin at laoreet nibh. Duis consequat orci vitae commodo euismod. Lorem ipsum dolor sit amet, consectetur adipiscing elit. Sed et turpis eget elit mollis aliquet. Quisque vulputate placerat dui, eu aliquam odio pretium ut. Aenean nec neque quis est euismod sodales.</p>
    <p>Aenean ac sapien vitae lacus ornare pretium. Maecenas sit amet blandit diam. Nunc ac mi elementum, dapibus nibh id, varius nulla. Pellentesque justo urna, imperdiet id vehicula nec, feugiat sed lectus. Mauris nunc est, porta cursus turpis vestibulum, dictum aliquam nibh. Mauris lorem lectus, convallis eget augue et, ullamcorper accumsan tortor. Curabitur lobortis, dui ut imperdiet euismod, mi diam pharetra odio, vel congue nunc libero dignissim nibh. Donec dapibus volutpat nisl at sodales. Vivamus id accumsan mi, sit amet porttitor elit. Sed blandit, dolor quis bibendum varius, magna felis egestas odio, vel tempor tellus diam a nisi. Nam sit amet imperdiet nisl. Quisque hendrerit metus sapien, id adipiscing lectus ultricies nec.</p>
    <a class="try-link" href="#">Enter your zipcode above to try it.</a>
  </article>

  <aside class="reviews">
    <h2><svg width="44" height="24" viewBox="0 0 44 24"><ellipse cx="26" cy="10" rx="16" ry="9" fill="#0c2d5c"/><ellipse cx="18" cy="12" rx="16" ry="9" fill="#d71f26"/><path d="M10 18L6 24L16 20Z" fill="#d71f26"/></svg>Visitors Reviews</h2>
    <p class="review-text">“Suspendisse lacinia ligula ac nibh sodales congue. Cras sed nibh eget nulla ultrices varius id in mauris. Vivamus sodales nibh vehicula neque vehicula, ut ultrices nisl egestas. Aliquam erat volutpat.”</p>
    <div class="review-name">-Name Here</div>
  </aside>

  <div class="social-box">
    <div class="social-head">Find us on Circlepage</div>
    <div class="social-page">
      <div class="social-mark"><span></span></div>
      <div><b>Auto Insurance</b> <span style="color:#3b5998">on circlepage</span><br><span class="like-btn"></span></div>
    </div>
    <div style="padding:0 6px">7,226 people like Auto insurance</div>
    <div class="fans" role="img" aria-label="Profile photos of followers">
      <div class="fan"><i></i>Sheri</div><div class="fan"><i></i>Cyn</div><div class="fan"><i></i>Toby</div><div class="fan"><i></i>Abel</div><div class="fan"><i></i>Dana</div>
      <div class="fan"><i></i>Lenny</div><div class="fan"><i></i>Jodi</div><div class="fan"><i></i>Robin</div><div class="fan"><i></i>June</div><div class="fan"><i></i>Ron</div>
    </div>
    <div class="social-foot">Circlepage social plugin</div>
  </div>
</main>

<footer class="site-footer">
  <a href="#">Home</a> | <a href="#">Privacy Policy</a> | <a href="#">Terms of Use</a><br>
  Copyright © 2013 policyhaven.example/Auto-Insurance. All Rights Reserved.
  <span class="badge"></span>
</footer>
</body>
</html>
```